New Business Card Design Project

Use the flyer uploaded and website www.brightoakbuilders.com for inspiration.
List Our Services on Backside of business cards
Marcus Delling
Harborline Builders Inc.
Licensed General Contractors
858-471-6093

Contact Information for Business Card

Use the flyer uploaded and website www.brightoakbuilders.com for inspiration. List Our Services on Backside of business cards Marcus Delling Harborline Builders Inc. Licensed General Contractors 858-471-6093

```html
<!DOCTYPE html>
<html lang="en">
<head>
<meta charset="utf-8">
<title>Harborline Builders – Business Card</title>
<link href="https://fonts.googleapis.com/css2?family=Marcellus&family=Arimo:wght@400&display=swap" rel="stylesheet">
<style>
  :root {
    --backdrop: #d9d9d9;
    --card: #303030;
    --ink: #ffffff;
    --serif: "Marcellus", serif;
    --sans: "Arimo", sans-serif;
  }
  * { margin: 0; padding: 0; box-sizing: border-box; }
  html, body { width: 1200px; height: 1040px; overflow: hidden; }
  body { background: var(--backdrop); position: relative; font-family: var(--sans); color: var(--ink); }

  .card {
    position: absolute; left: 284px; width: 644px; height: 368px;
    background: var(--card); border-radius: 18px;
    box-shadow: 0 3px 6px rgba(0,0,0,.25);
  }
  .card--front { top: 130px; }
  .card--back { top: 567px; }
  .abs { position: absolute; white-space: nowrap; }

  /* front */
  .brand-name {
    left: 0; width: 326px; top: 210px; text-align: center;
    font-family: var(--serif); font-size: 19px; letter-spacing: 1px; text-transform: uppercase;
  }
  .divider { left: 326px; top: 128px; width: 1.5px; height: 114px; background: var(--ink); }
  .person-name {
    left: 344px; top: 124px; font-family: var(--serif); font-size: 24px; letter-spacing: 1px; text-transform: uppercase;
  }
  .contact-list { left: 350px; top: 174px; list-style: none; font-size: 16px; line-height: 20px; }
  .contact-list li { display: flex; align-items: center; gap: 8px; }
  .contact-list svg { width: 13px; height: 13px; fill: var(--ink); flex: none; }
  .footer-line { top: 324px; font-size: 16px; }
  .footer-company { left: 98px; }
  .footer-license { left: 318px; }

  /* back */
  .back-brand {
    left: 0; width: 100%; top: 94px; text-align: center;
    font-family: var(--serif); font-size: 30px; letter-spacing: 2px; text-transform: uppercase;
  }
  .services-title {
    left: 0; width: 100%; top: 215px; text-align: center;
    font-family: var(--serif); font-size: 20px; letter-spacing: 3px;
  }
  .services-list { left: 0; width: 100%; top: 250px; text-align: center; list-style: none; font-size: 16px; line-height: 23.5px; }
  .services-list .sep {
    display: inline-block; width: 7px; height: 7px; background: var(--ink);
    margin: 0 11px; vertical-align: 2px;
  }
</style>
</head>
<body>

<section class="card card--front">
  <div class="abs brand-name">Harborline Builders</div>
  <div class="abs divider"></div>
  <div class="abs person-name">Marcus Delling</div>
  <ul class="abs contact-list">
    <li><svg viewBox="0 0 24 24" aria-hidden="true"><path d="M6.6 10.8a15.1 15.1 0 0 0 6.6 6.6l2.2-2.2a1 1 0 0 1 1-.25 11.4 11.4 0 0 0 3.6.57 1 1 0 0 1 1 1V20a1 1 0 0 1-1 1A17 17 0 0 1 3 4a1 1 0 0 1 1-1h3.5a1 1 0 0 1 1 1c0 1.25.2 2.45.57 3.57a1 1 0 0 1-.25 1z"/></svg>858-471-6093</li>
    <li><svg viewBox="0 0 24 24" aria-hidden="true"><path d="M2 5h20v14H2z M3.5 6.5 12 13l8.5-6.5" fill="none" stroke="#fff" stroke-width="2"/></svg>info@brightoakbuilders.com</li>
    <li><svg viewBox="0 0 24 24" aria-hidden="true"><circle cx="12" cy="12" r="10"/><path d="M8 6c2 1 1 3 3 4s0 3 2 4M15 5c-1 2 1 3 3 3" stroke="#303030" stroke-width="2" fill="none"/></svg>www.brightoakbuilders.com</li>
  </ul>
  <div class="abs footer-line footer-company">Harborline Builders Inc.</div>
  <div class="abs footer-line footer-license">Licensed General Contractors</div>
</section>

<section class="card card--back">
  <div class="abs back-brand">Harborline Builders</div>
  <div class="abs services-title">SERVICES</div>
  <ul class="abs services-list">
    <li>Remodel : Kitchen &amp; Bath<span class="sep"></span>Painting : Interior &amp; Exterior</li>
    <li>Flooring : Carpet, Vinyl, Wood<span class="sep"></span>Window &amp; Door Replacement</li>
    <li>Plumbing : Repairs &amp; Upgrades<span class="sep"></span>Energy- Efficient Upgrades</li>
    <li>Deck &amp; Pation Construction<span class="sep"></span>Water &amp; Mold Damage<span class="sep"></span>Garage Renovation</li>
  </ul>
</section>

</body>
</html>
```